Social Media Graphics - Oakline Push REVISED

Create 6-7 individual social media graphics (square size) to encourage folks to join our online course called:

The Harvest Ledger Circle
How to Launch a Multi-Million Business From Scratch
Sign Up Today!

IMPORTANT: Make the largest and most prominent text on the graphic be: How to Launch a Multi-Million Business From Scratch

For the color scheme of the graphics, let's try a blue color palette; make sure the graphics appeal to both men and women

Make sure each graphic contains 1 of the 3 pics attached (crop pic as needed); and make sure one of the graphics is all TEXT only.

Target Market(s)

men and women looking to start a business

Industry/Entity Type

Entrepreneurship

Colors
0054AA
0677BA
7BADD7
CADEEF
E8F1F8

Requirements
Must have
• All the text and use the 3 pics provided; one graphic can be all text; Simple, modern design that's easy to read

```html
<!DOCTYPE html>
<html lang="en">
<head>
<meta charset="utf-8">
<title>The Harvest Ledger Circle – Sign Up</title>
<link rel="stylesheet" href="https://fonts.googleapis.com/css2?family=Anton&family=Oswald:wght@600&family=Roboto:wght@400&display=swap">
<style>
  :root {
    --navy: #003a78;
    --blue-strong: #0054aa;
    --blue-mid: #0677ba;
    --blue-soft: #7badd7;
    --blue-pale: #cadeef;
    --blue-mist: #e8f1f8;
    --paper: #ffffff;
  }
  html, body {
    margin: 0;
    padding: 0;
    width: 1200px;
    height: 1200px;
    overflow: hidden;
    background: var(--navy);
  }
  .graphic {
    display: block;
    width: 1200px;
    height: 1200px;
  }
  .backdrop { fill: var(--navy); }
  .band { fill: url(#blueSweep); }
  .program-name {
    font-family: "Anton", "Oswald", sans-serif;
    fill: var(--navy);
  }
  .headline-strong {
    font-family: "Anton", "Oswald", sans-serif;
  }
  .headline-light {
    font-family: "Roboto", "Arial", sans-serif;
    font-weight: 400;
  }
  .is-white { fill: var(--paper); }
  .is-pale { fill: var(--blue-pale); }
  .is-soft { fill: var(--blue-soft); }
  .cta-button { fill: var(--blue-mid); stroke: var(--paper); stroke-width: 4; }
  .cta-label {
    font-family: "Oswald", sans-serif;
    font-weight: 600;
    fill: var(--paper);
  }
  .pointer { fill: var(--navy); stroke: var(--paper); stroke-width: 3; stroke-linejoin: round; }
  .click-marks { stroke: var(--navy); stroke-width: 3; stroke-linecap: round; fill: none; }
</style>
</head>
<body>
<svg class="graphic" viewBox="0 0 1200 1200" xmlns="http://www.w3.org/2000/svg">
  <defs>
    <linearGradient id="blueSweep" x1="0" y1="0" x2="1" y2="0">
      <stop offset="0" stop-color="#7badd7"/>
      <stop offset="0.22" stop-color="#e8f1f8"/>
      <stop offset="0.5" stop-color="#cadeef"/>
      <stop offset="0.72" stop-color="#7badd7"/>
      <stop offset="1" stop-color="#e8f1f8"/>
    </linearGradient>
  </defs>

  <rect class="backdrop" x="0" y="0" width="1200" height="1200"/>

  <path class="band band-top" d="M0 0 H1200 V112 Q600 345 0 117 Z"/>
  <path class="band band-bottom" d="M0 1111 Q600 945 1200 1111 V1200 H0 Z"/>

  <text class="program-name" x="600" y="132" font-size="78" text-anchor="middle" textLength="780" lengthAdjust="spacingAndGlyphs">THE HARVEST LEDGER CIRCLE</text>

  <text class="headline-light is-pale" x="600" y="368" font-size="100" text-anchor="middle" textLength="950" lengthAdjust="spacingAndGlyphs">HOW TO LAUNCH A</text>
  <text class="headline-strong is-white" x="600" y="562" font-size="200" text-anchor="middle" textLength="950" lengthAdjust="spacingAndGlyphs">MULTI-MILLION</text>
  <text class="headline-strong is-soft" x="600" y="784" font-size="230" text-anchor="middle" textLength="950" lengthAdjust="spacingAndGlyphs">BUSINESS</text>
  <text class="headline-light is-pale" x="600" y="878" font-size="100" text-anchor="middle" textLength="950" lengthAdjust="spacingAndGlyphs">FROM SCRATCH</text>

  <rect class="cta-button" x="403" y="918" width="394" height="96" rx="12"/>
  <text class="cta-label" x="600" y="996" font-size="76" text-anchor="middle" textLength="350" lengthAdjust="spacingAndGlyphs">SIGN UP TODAY!</text>

  <g class="click-marks">
    <line x1="757" y1="994" x2="757" y2="984"/>
    <line x1="745" y1="1000" x2="737" y2="993"/>
    <line x1="769" y1="1000" x2="777" y2="993"/>
    <line x1="742" y1="1011" x2="732" y2="1011"/>
    <line x1="745" y1="1022" x2="737" y2="1028"/>
  </g>
  <path class="pointer" d="M757 1006 L757 1062 L770 1050 L781 1074 L791 1069 L780 1046 L798 1045 Z"/>
</svg>
</body>
</html>
```